Global (re)insurance broker needs a business card design

We need a classic business card for our company that is headquartered in SG, with offices in Malaysia and Dubai. We specialise in insurance and reinsurance broking and consultancy for our global clients.

```html
<!DOCTYPE html>
<html lang="en">
<head>
<meta charset="UTF-8">
<title>Norvale Business Card</title>
<link rel="stylesheet" href="https://fonts.googleapis.com/css2?family=Montserrat:wght@700;800&family=Open+Sans:wght@400;600&display=swap">
<style>
  :root {
    --page-bg: #2b2b2e;
    --card-bg: #161616;
    --brand-blue: #2a4a9c;
    --brand-mint: #c4dcb8;
    --text-light: #f2f2f2;
  }
  * { margin: 0; padding: 0; box-sizing: border-box; }
  html, body {
    width: 1200px;
    height: 947px;
    overflow: hidden;
    background: var(--page-bg);
  }
  .canvas {
    position: relative;
    width: 1200px;
    height: 947px;
  }
  .card {
    position: absolute;
    width: 580px;
    height: 330px;
    background: var(--card-bg);
    border: 3px solid var(--brand-blue);
    border-radius: 26px;
    overflow: hidden;
    box-shadow: 0 18px 40px rgba(0,0,0,0.45);
  }
  .card--front { left: 70px; top: 90px; }
  .card--back { left: 550px; top: 520px; }

  .brand-name {
    font-family: "Montserrat", sans-serif;
    font-weight: 800;
    color: var(--brand-mint);
    letter-spacing: 0.04em;
    line-height: 1;
    white-space: nowrap;
  }
  .card--front .brand-name {
    position: absolute;
    left: 0; right: 0; top: 50%;
    transform: translateY(-50%);
    text-align: center;
    font-size: 84px;
  }
  .card--back .brand-name {
    position: absolute;
    left: 34px;
    top: 132px;
    font-size: 34px;
  }

  .divider {
    position: absolute;
    left: 262px;
    top: 34px;
    width: 2px;
    height: 200px;
    background: var(--brand-mint);
  }
  .contact {
    position: absolute;
    left: 284px;
    top: 30px;
    font-family: "Open Sans", sans-serif;
    color: var(--text-light);
  }
  .contact__name {
    font-family: "Montserrat", sans-serif;
    font-weight: 700;
    font-size: 21px;
    color: var(--brand-mint);
  }
  .contact__name .given { color: var(--brand-blue); }
  .contact__title {
    font-size: 14px;
    margin-top: 2px;
  }
  .contact__list {
    list-style: none;
    margin-top: 14px;
    font-size: 13px;
    line-height: 1.6;
  }
  .contact__list li {
    display: flex;
    align-items: center;
    gap: 7px;
  }
  .contact__list svg { width: 12px; height: 12px; flex: none; }
  .contact__address {
    margin-top: 14px;
    font-size: 13px;
    line-height: 1.45;
    font-style: normal;
  }
  .swoosh {
    position: absolute;
    left: 0; bottom: 0;
    width: 100%;
    height: 100%;
    pointer-events: none;
  }
</style>
</head>
<body>
<main class="canvas">
  <section class="card card--front" aria-label="Card front">
    <p class="brand-name">NORVALE</p>
  </section>

  <section class="card card--back" aria-label="Card back">
    <svg class="swoosh" viewBox="0 0 580 330" preserveAspectRatio="none" aria-hidden="true">
      <path d="M120 330 C 300 305, 480 245, 580 178 L 580 330 Z" fill="var(--brand-blue)"/>
      <path d="M120 318 C 300 294, 470 236, 570 166" fill="none" stroke="var(--brand-mint)" stroke-width="5" stroke-linecap="round"/>
    </svg>

    <p class="brand-name">NORVALE</p>
    <div class="divider"></div>

    <div class="contact">
      <p class="contact__name"><span class="given">Mira</span> Lau</p>
      <p class="contact__title">Chief Operating Officer</p>
      <ul class="contact__list">
        <li>
          <svg viewBox="0 0 12 12"><path d="M3 1 L5 3.5 L4 5 Q5 7 7 8 L8.5 7 L11 9 L9.5 11 Q4 10 1 3 Z" fill="var(--text-light)"/></svg>
          +65 8123 4560
        </li>
        <li>
          <svg viewBox="0 0 12 12"><rect x="1" y="2.5" width="10" height="7" fill="var(--text-light)"/><path d="M1 2.5 L6 7 L11 2.5" fill="none" stroke="var(--card-bg)" stroke-width="1"/></svg>
          mira@norvale.com
        </li>
        <li>
          <svg viewBox="0 0 12 12"><circle cx="6" cy="6" r="5" fill="none" stroke="var(--text-light)" stroke-width="1.4"/><path d="M1 6 H11 M6 1 Q3 6 6 11 Q9 6 6 1" fill="none" stroke="var(--text-light)" stroke-width="1"/></svg>
          www.norvale.com
        </li>
      </ul>
      <address class="contact__address">
        22 Harbour Street,<br>
        Meridian Tower #08-04,<br>
        Singapore 048620
      </address>
    </div>
  </section>
</main>
</body>
</html>
```